Business Card Design for RB Wine:

I'm looking for a card that has the following.
Front:
- Merlot Colored
- stripe down the middle in silver or gold flake
- RB in block like thick letters with gold or silver flake above stripe
-Wine: below stripe
- a grape bunch that is at the end of the stripe that is made so it can be printed as embossed
Back:
- line down the middle of card in Merlot, card is white background
- to the left Marisa Dutton, (next line) Owner, (next line) Certified Sommelier, GVA
- to the right (listed) restaurant consulting, wine tours, personal tastings, event planning, personal wine buying
- add embossed grape bunch
Also, looking for a piece that slides over like a envelope for a room key for a hotel that says "We met @ PALVIN" and possibly a file for that, that I can edit.
Would like card to be printed on a thicker cardstock

```html
<!DOCTYPE html>
<html lang="en">
<head>
<meta charset="utf-8">
<title>RB Wine – Business Card</title>
<link rel="stylesheet" href="https://fonts.googleapis.com/css2?family=Source+Sans+3:wght@400;600&display=swap">
<style>
  :root {
    --stage: #111111;
    --merlot: #7d171f;
    --merlot-text: #7a1519;
    --gold-light: #d7a53a;
    --gold-mid: #c8952f;
    --gold-dark: #a97a1e;
    --silver: #d6d6d6;
    --paper: #f3f3f3;
    --ink: #2b2b2b;
    --grape-dark: #2f2f2f;
    --grape-light: #ffffff;
  }
  * { margin: 0; padding: 0; box-sizing: border-box; }
  html, body {
    width: 1200px; height: 900px; overflow: hidden;
    background: var(--stage);
  }
  .canvas { position: relative; width: 1200px; height: 900px; }
  .card {
    position: absolute; top: 306px;
    width: 440px; height: 271px;
    border-radius: 12px;
    overflow: hidden;
    box-shadow: 2px 4px 8px rgba(0,0,0,0.6);
  }
  .card--front { left: 149px; background: var(--merlot); }
  .card--back  { left: 608px; background: var(--paper); }

  .brand-name {
    font-family: "Source Sans 3", sans-serif;
    font-weight: 600;
    color: var(--silver);
  }
  .brand-name__initials {
    position: absolute; left: 0; width: 440px; top: 42px;
    text-align: center;
    font-size: 96px; line-height: 1;
  }
  .brand-name__word {
    position: absolute; left: 0; width: 440px; top: 178px;
    text-align: center;
    font-size: 26px; line-height: 1;
    letter-spacing: 1px;
  }
  .stripe {
    position: absolute; left: 0; right: 0; top: 148px; height: 23px;
    background: linear-gradient(180deg, var(--gold-light) 0%, var(--gold-mid) 50%, var(--gold-dark) 100%);
  }
  .grape-spot {
    position: absolute; border-radius: 45% 45% 50% 50%;
  }
  .grape-spot--front {
    left: 322px; top: 111px; width: 90px; height: 105px;
    background: var(--grape-light);
  }
  .divider {
    position: absolute; left: 191px; top: 0; bottom: 0; width: 2px;
    background: var(--merlot);
  }
  .identity {
    position: absolute; left: 32px; top: 104px;
    font-family: "Source Sans 3", sans-serif;
    color: var(--ink); font-size: 12.5px; line-height: 19px;
  }
  .identity__name {
    font-size: 18px; font-weight: 600; color: var(--merlot-text);
    letter-spacing: 0.3px; line-height: 22px; margin-bottom: 1px;
  }
  .services {
    position: absolute; left: 212px; top: 96px;
    list-style: none;
    font-family: "Source Sans 3", sans-serif;
    font-size: 12.5px; line-height: 16px; color: var(--ink);
  }
  .services li { position: relative; padding-left: 15px; }
  .services li::before {
    content: ""; position: absolute; left: 0; top: 5px;
    width: 7px; height: 7px; border-radius: 50%;
    background: var(--merlot);
  }
  .grape-spot--back {
    left: 345px; top: 154px; width: 72px; height: 84px;
    background: var(--grape-dark);
  }
</style>
</head>
<body>
<main class="canvas">
  <section class="card card--front" aria-label="Card front">
    <div class="brand-name" aria-label="RB Wine">
      <span class="brand-name__initials">RB</span>
      <span class="brand-name__word">Wine</span>
    </div>
    <div class="stripe"></div>
    <div class="grape-spot grape-spot--front" role="img" aria-label="Embossed grape bunch emblem"></div>
  </section>

  <section class="card card--back" aria-label="Card back">
    <div class="divider"></div>
    <div class="identity">
      <p class="identity__name">MARISA DUTTON</p>
      <p>Owner</p>
      <p>Certified Sommelier, GVA</p>
    </div>
    <ul class="services">
      <li>Restaurant Consulting</li>
      <li>Wine Tours</li>
      <li>Personal Tastings</li>
      <li>Event Planning</li>
      <li>Personal wine buying</li>
    </ul>
    <div class="grape-spot grape-spot--back" role="img" aria-label="Embossed grape bunch emblem"></div>
  </section>
</main>
</body>
</html>
```